Banner poster with different motifs

I'm looking for 5 banners and posters in A1 format in the same design, or the similarity must be recognizable...
Kept quite simple with different titles.

1 ballet
2 Contemporary Dance
3 high heels
4 Salsa & Bachata & Zouk
5 Hip Hop

Modern bright colors
it is for the entrance so that the students see here is a dance school

The text may also be included in the image
The photos are for guidance only; some are our own, some are purchased. However, we are permitted to use them, including our logo, of course.

```html
<!DOCTYPE html>
<html lang="en">
<head>
<meta charset="utf-8">
<title>High Heels – Poster and Banner</title>
<link rel="stylesheet" href="https://fonts.googleapis.com/css2?family=Anton&family=Josefin+Sans:wght@300;400&family=Poppins:ital,wght@0,600;1,800&display=swap">
<style>
  :root {
    --sheet-bg: #ebebeb;
    --night: #0c0518;
    --hot-pink: #ff12c4;
    --white: #ffffff;
    --label-ink: #3b3b3b;
  }
  * { margin: 0; padding: 0; box-sizing: border-box; }
  html, body {
    width: 1200px; height: 2639px; overflow: hidden;
    background: var(--sheet-bg);
  }
  .sheet { position: relative; width: 1200px; height: 2639px; }
  .artboard {
    position: absolute; left: 109px;
    box-shadow: 0 18px 28px rgba(0,0,0,0.45);
    background: var(--night);
  }
  .artboard svg { display: block; }
  .artboard--poster { top: 152px; width: 982px; height: 1389px; }
  .artboard--banner { top: 1718px; width: 982px; height: 693px; }
  .format-label {
    position: absolute; left: 0; width: 1200px; text-align: center;
    font-family: "Poppins", sans-serif; font-weight: 800; font-style: italic;
    font-size: 38px; letter-spacing: 7px; color: var(--label-ink);
  }
  .format-label--poster { top: 1598px; }
  .format-label--banner { top: 2471px; }
  .brand-name { font-family: "Josefin Sans", sans-serif; font-weight: 300; fill: var(--white); }
  .brand-tagline { font-family: "Josefin Sans", sans-serif; font-weight: 400; fill: var(--white); }
  .headline text { font-family: "Anton", sans-serif; fill: url(#pinkFill); }
  .web-address { font-family: "Poppins", sans-serif; font-weight: 600; fill: var(--white); }
  .web-address .accent { fill: var(--hot-pink); }
</style>
</head>
<body>
<div class="sheet">

  <!-- Poster -->
  <div class="artboard artboard--poster">
    <svg width="982" height="1389" viewBox="0 0 982 1389">
      <defs>
        <radialGradient id="bgGlow" cx="0.55" cy="0.45" r="0.75">
          <stop offset="0" stop-color="#3a2450"/>
          <stop offset="0.55" stop-color="#140828"/>
          <stop offset="1" stop-color="#04020a"/>
        </radialGradient>
        <linearGradient id="beam" x1="1" y1="0" x2="0.3" y2="0.8">
          <stop offset="0" stop-color="#ffffff" stop-opacity="0.85"/>
          <stop offset="0.5" stop-color="#c8b8d8" stop-opacity="0.3"/>
          <stop offset="1" stop-color="#8a6aa8" stop-opacity="0"/>
        </linearGradient>
        <radialGradient id="waveGlow" cx="0.5" cy="0.5" r="0.5">
          <stop offset="0" stop-color="#8e2ad0" stop-opacity="0.75"/>
          <stop offset="1" stop-color="#3a0f70" stop-opacity="0"/>
        </radialGradient>
        <linearGradient id="pinkFill" x1="0" y1="0" x2="1" y2="1">
          <stop offset="0" stop-color="#ff2ccd"/>
          <stop offset="0.5" stop-color="#ff5ad6"/>
          <stop offset="1" stop-color="#ff0cbf"/>
        </linearGradient>
        <linearGradient id="dancerTone" x1="0" y1="0" x2="0" y2="1">
          <stop offset="0" stop-color="#b07a5e"/>
          <stop offset="0.3" stop-color="#2a1c22"/>
          <stop offset="0.45" stop-color="#a06a50"/>
          <stop offset="0.55" stop-color="#101014"/>
          <stop offset="1" stop-color="#0a0a0e"/>
        </linearGradient>
        <radialGradient id="floor" cx="0.5" cy="0.5" r="0.5">
          <stop offset="0" stop-color="#8a6a9a" stop-opacity="0.8"/>
          <stop offset="1" stop-color="#3a1a50" stop-opacity="0"/>
        </radialGradient>
        <filter id="soft"><feGaussianBlur stdDeviation="18"/></filter>
      </defs>
      <rect width="982" height="1389" fill="url(#bgGlow)"/>
      <ellipse cx="860" cy="980" rx="320" ry="160" fill="url(#waveGlow)" role="img" aria-label="Flowing violet light waves"/>
      <ellipse cx="140" cy="800" rx="260" ry="170" fill="url(#waveGlow)" opacity="0.7"/>
      <polygon points="940,0 982,0 982,60 640,720 420,620" fill="url(#beam)" filter="url(#soft)"/>

      <circle cx="491" cy="114" r="52" fill="none" stroke="var(--white)" stroke-width="3"/>
      <text class="brand-name" x="491" y="219" text-anchor="middle" font-size="46" letter-spacing="4">VELARA</text>
      <text class="brand-tagline" x="491" y="244" text-anchor="middle" font-size="15" letter-spacing="3.2">DANCE CENTER FRANKFURT</text>

      <g class="headline" aria-label="HIGH HEELS">
        <text x="163" y="716" font-size="442" textLength="165" lengthAdjust="spacingAndGlyphs">H</text>
        <text x="362" y="716" font-size="442" textLength="75" lengthAdjust="spacingAndGlyphs">I</text>
        <text x="471" y="716" font-size="442" textLength="165" lengthAdjust="spacingAndGlyphs">G</text>
        <text x="670" y="716" font-size="442" textLength="165" lengthAdjust="spacingAndGlyphs">H</text>

        <text x="163" y="1178" font-size="510" textLength="150" lengthAdjust="spacingAndGlyphs">H</text>
        <text x="325" y="1178" font-size="510" textLength="120" lengthAdjust="spacingAndGlyphs">E</text>
        <text x="457" y="1178" font-size="510" textLength="120" lengthAdjust="spacingAndGlyphs">E</text>
        <text x="589" y="1178" font-size="510" textLength="115" lengthAdjust="spacingAndGlyphs">L</text>
        <text x="716" y="1178" font-size="510" textLength="130" lengthAdjust="spacingAndGlyphs">S</text>
      </g>

      <ellipse cx="491" cy="1240" rx="330" ry="46" fill="url(#floor)"/>
      <rect x="400" y="300" width="170" height="920" rx="50" fill="url(#dancerTone)" role="img" aria-label="Photo of a dancer posing in high-heel boots, arms raised"/>

      <text class="web-address" x="491" y="1326" text-anchor="middle" font-size="24" letter-spacing="18">www.<tspan class="accent">velara</tspan>.de</text>
    </svg>
  </div>
  <div class="format-label format-label--poster">A1 POSTER</div>

  <!-- Banner -->
  <div class="artboard artboard--banner">
    <svg width="982" height="693" viewBox="0 0 982 693">
      <defs>
        <radialGradient id="bgGlowB" cx="0.55" cy="0.5" r="0.7">
          <stop offset="0" stop-color="#2e1a44"/>
          <stop offset="0.6" stop-color="#120724"/>
          <stop offset="1" stop-color="#04020a"/>
        </radialGradient>
        <filter id="softB"><feGaussianBlur stdDeviation="14"/></filter>
      </defs>
      <rect width="982" height="693" fill="url(#bgGlowB)"/>
      <ellipse cx="200" cy="260" rx="280" ry="150" fill="url(#waveGlow)" role="img" aria-label="Flowing violet light waves"/>
      <ellipse cx="820" cy="400" rx="260" ry="120" fill="url(#waveGlow)" opacity="0.85"/>
      <polygon points="930,0 982,0 982,50 720,420 540,330" fill="url(#beam)" filter="url(#softB)"/>

      <circle cx="491" cy="65" r="33" fill="none" stroke="var(--white)" stroke-width="2"/>
      <text class="brand-name" x="491" y="125" text-anchor="middle" font-size="29" letter-spacing="2.5">VELARA</text>
      <text class="brand-tagline" x="491" y="137" text-anchor="middle" font-size="10" letter-spacing="2">DANCE CENTER FRANKFURT</text>

      <g class="headline" aria-label="HIGH HEELS">
        <text x="323" y="395" font-size="234" textLength="85" lengthAdjust="spacingAndGlyphs">H</text>
        <text x="426" y="395" font-size="234" textLength="39" lengthAdjust="spacingAndGlyphs">I</text>
        <text x="483" y="395" font-size="234" textLength="85" lengthAdjust="spacingAndGlyphs">G</text>
        <text x="586" y="395" font-size="234" textLength="85" lengthAdjust="spacingAndGlyphs">H</text>

        <text x="323" y="637" font-size="269" textLength="77" lengthAdjust="spacingAndGlyphs">H</text>
        <text x="406" y="637" font-size="269" textLength="61" lengthAdjust="spacingAndGlyphs">E</text>
        <text x="473" y="637" font-size="269" textLength="61" lengthAdjust="spacingAndGlyphs">E</text>
        <text x="540" y="637" font-size="269" textLength="59" lengthAdjust="spacingAndGlyphs">L</text>
        <text x="605" y="637" font-size="269" textLength="67" lengthAdjust="spacingAndGlyphs">S</text>
      </g>

      <ellipse cx="491" cy="650" rx="200" ry="26" fill="url(#floor)"/>
      <rect x="438" y="178" width="90" height="487" rx="28" fill="url(#dancerTone)" role="img" aria-label="Photo of a dancer posing in high-heel boots, arms raised"/>
    </svg>
  </div>
  <div class="format-label format-label--banner">A1 BANNER</div>

</div>
</body>
</html>
```